GJ & DW Fencing Pty Ltd

We already have an existing logo created by Pixel Harbour however we have restructured to a company. We would like someone to add Pty Ltd to our business name please.

Colors

Designer to choose only greyscale colors for use in the design.

```html
<!DOCTYPE html>
<html lang="en">
<head>
<meta charset="utf-8">
<title>GJ &amp; DW Fencing Pty Ltd – Business Card</title>
<link rel="stylesheet" href="https://fonts.googleapis.com/css2?family=Lora:wght@400;600;700&display=swap">
<style>
  :root {
    --page-bg: #d4d2cf;
    --card-top: #f4f4f3;
    --card-bottom: #e2e2e1;
    --card-edge: #bdbdbc;
    --card-shadow: rgba(0, 0, 0, 0.28);
    --ink: #161616;
    --ink-soft: #2b2b2b;
  }
  * { box-sizing: border-box; margin: 0; padding: 0; }
  html, body {
    width: 1200px;
    height: 970px;
    overflow: hidden;
    background: var(--page-bg);
  }
  .canvas {
    position: relative;
    width: 1200px;
    height: 970px;
  }
  .card {
    position: absolute;
    left: 100px;
    top: 208px;
    width: 1000px;
    height: 553px;
    border-radius: 24px;
    background: linear-gradient(180deg, var(--card-top) 0%, var(--card-bottom) 100%);
    border: 1px solid var(--card-edge);
    box-shadow: 0 6px 0 #1c1c1c, 0 18px 40px var(--card-shadow);
    font-family: "Lora", Georgia, serif;
    color: var(--ink);
  }
  .brand {
    position: absolute;
    right: 64px;
    top: 96px;
    text-align: right;
    font-weight: 600;
    color: var(--ink);
    line-height: 1;
  }
  .brand-main {
    display: block;
    font-size: 84px;
    letter-spacing: 1px;
  }
  .brand-sub {
    display: block;
    margin-top: 14px;
    font-size: 38px;
  }
  .person-name {
    position: absolute;
    left: 56px;
    top: 372px;
    font-size: 29px;
    font-weight: 700;
    letter-spacing: 0.5px;
    color: var(--ink-soft);
  }
  .person-role {
    position: absolute;
    left: 56px;
    top: 408px;
    font-size: 22px;
    color: var(--ink-soft);
  }
  .divider {
    position: absolute;
    left: 180px;
    right: 64px;
    top: 424px;
    height: 3px;
    background: var(--ink);
  }
  .contact-list {
    position: absolute;
    left: 56px;
    top: 460px;
    list-style: none;
  }
  .contact-item {
    display: flex;
    align-items: center;
    gap: 16px;
    height: 32px;
    font-size: 23px;
    color: var(--ink-soft);
  }
  .contact-icon { width: 26px; height: 26px; flex: none; }
  .company-block {
    position: absolute;
    left: 596px;
    top: 458px;
    font-size: 23px;
    line-height: 36px;
    color: var(--ink-soft);
  }
  .company-name { font-weight: 700; }
</style>
</head>
<body>
<div class="canvas">
  <article class="card">
    <div class="brand">
      <span class="brand-main">GJ &amp; DW</span>
      <span class="brand-sub">Fencing Pty Ltd</span>
    </div>

    <h1 class="person-name">CALLUM REID</h1>
    <p class="person-role">President</p>
    <div class="divider"></div>

    <ul class="contact-list">
      <li class="contact-item">
        <svg class="contact-icon" viewBox="0 0 26 26" aria-hidden="true">
          <circle cx="13" cy="13" r="13" fill="#161616"/>
          <rect x="9" y="6" width="8" height="14" rx="1.5" fill="none" stroke="#f2f2f2" stroke-width="1.6"/>
          <circle cx="13" cy="17.3" r="0.9" fill="#f2f2f2"/>
        </svg>
        <span>Greg 0491570156</span>
      </li>
      <li class="contact-item">
        <svg class="contact-icon" viewBox="0 0 26 26" aria-hidden="true">
          <circle cx="13" cy="13" r="13" fill="#161616"/>
          <rect x="7" y="8.5" width="12" height="9" rx="1" fill="#f2f2f2"/>
          <path d="M7.4 9 L13 13.6 L18.6 9" fill="none" stroke="#161616" stroke-width="1.4"/>
        </svg>
        <span>gjdwfencing@mailbox.com</span>
      </li>
    </ul>

    <address class="company-block" style="font-style: normal;">
      <div class="company-name">GJ &amp; DW Fencing Pty Ltd</div>
      <div>PO Box 418 Merredin WA 6415</div>
    </address>
  </article>
</div>
</body>
</html>
```